Business Card Design

Hi I need a business card designed, we already have the business name logo artwork and would like some concept ideas for the Bus Card layout.
On the back of the card i want to include the products and services that we offer.
We are a Plastics Sheeting manufacture based in Perth Australia.

                                       

We need a BC design for a company called Tarvo Plastics based in Perth Australia.

We supply from DIY to Trade & Industrial  Engineering Markets.

We specialise in:

·         Cut to size panels  (all shapes and sizes)

·         Plastics fabrication & Welding

·         Custom Designs

·         Plastic Repairs

·         PVC Pipe Slotting & PVC Pipe Threading

·         Supplier of all types of engineering plastics and profiles.

Including:           Acrylic / Clarvene

                               Polycarbonate / Dorvil

                               Prismatic Light Diffuser

                               Vantrib

                               HDPE / UHMWPE

                               PVC / PVC Foam

                               Nylon

                               HIPS

```html
<!DOCTYPE html>
<html lang="en">
<head>
<meta charset="utf-8">
<title>Tarvo Plastics – Business Card</title>
<link rel="stylesheet" href="https://fonts.googleapis.com/css2?family=Open+Sans:ital,wght@0,400;0,600;0,700;1,700&display=swap">
<style>
  :root {
    --navy: #1b2a57;
    --orange: #e07128;
    --white: #ffffff;
    --grey-text: #555a63;
    --bullet: #2b6fb6;
    --bg: #e6e7ec;
  }
  * { margin: 0; padding: 0; box-sizing: border-box; }
  html, body { width: 1200px; height: 987px; overflow: hidden; }
  body {
    background: var(--bg);
    font-family: "Open Sans", Arial, sans-serif;
    position: relative;
  }
  .card {
    position: absolute;
    left: 240px;
    width: 720px;
    height: 436px;
    border-radius: 26px;
    background: var(--white);
    overflow: hidden;
    box-shadow: 0 6px 18px rgba(0,0,0,0.18);
  }
  .card-front { top: 36px; }
  .card-back { top: 515px; }

  /* Front */
  .brand {
    position: absolute;
    top: 50px; left: 0; right: 0;
    display: flex; align-items: center; justify-content: center; gap: 16px;
    color: var(--navy);
    font-weight: 700;
    font-size: 64px;
    letter-spacing: -1px;
  }
  .brand-mark { width: 26px; height: 26px; background: var(--navy); }
  .contact-band {
    position: absolute;
    top: 176px; left: 0; right: 0; height: 196px;
    background: var(--orange);
    color: var(--white);
    display: flex; justify-content: center; align-items: center;
  }
  .address {
    font-style: normal;
    text-align: right;
    font-size: 17px;
    line-height: 1.45;
    padding-right: 26px;
  }
  .divider { width: 1px; height: 140px; background: rgba(255,255,255,0.75); }
  .contacts {
    list-style: none;
    padding-left: 26px;
    font-size: 19px;
    line-height: 1.75;
  }
  .contacts li { display: flex; align-items: center; gap: 10px; }
  .contacts svg { width: 18px; height: 18px; fill: var(--white); flex: none; }
  .name-band {
    position: absolute;
    bottom: 0; left: 0; right: 0; height: 64px;
    background: var(--navy);
    color: var(--white);
    display: flex; align-items: center; justify-content: center;
    font-size: 24px;
  }
  .person-name { font-weight: 700; }
  .person-title { font-weight: 400; font-size: 20px; margin-left: 6px; }

  /* Back */
  .back-content {
    position: absolute; inset: 0;
    padding: 24px 36px;
    display: flex; flex-direction: column; justify-content: center;
    text-align: center;
    color: var(--navy);
  }
  .markets {
    font-style: italic; font-weight: 700;
    font-size: 20px; line-height: 1.3;
    margin-bottom: 12px;
  }
  .section-title { font-weight: 700; font-size: 25px; line-height: 1.3; margin: 2px 0 4px; }
  .offer-list {
    list-style: none;
    color: var(--grey-text);
    font-size: 18px;
    line-height: 1.5;
    margin-bottom: 8px;
  }
  .offer-list span { white-space: nowrap; }
  .offer-list span::before { content: "\2022"; color: var(--bullet); margin: 0 5px 0 12px; }
</style>
</head>
<body>

<section class="card card-front" aria-label="Business card front">
  <div class="brand"><span class="brand-mark"></span><span>Tarvo Plastics</span></div>
  <div class="contact-band">
    <address class="address">
      Unit 4/18 Kelvar Circuit<br>
      Halden Park WA 6158<br>
      PO Box 2284<br>
      Halden Park DC WA 6972<br>
      Kestrel Trading Pty Ltd<br>
      T/A Tarvo Plastics ABN: TBA
    </address>
    <div class="divider"></div>
    <ul class="contacts">
      <li><svg viewBox="0 0 24 24" aria-hidden="true"><path d="M6.6 10.8a15.1 15.1 0 0 0 6.6 6.6l2.2-2.2c.3-.3.7-.4 1-.2 1.1.4 2.3.6 3.6.6.6 0 1 .4 1 1V20c0 .6-.4 1-1 1A17 17 0 0 1 3 4c0-.6.4-1 1-1h3.5c.6 0 1 .4 1 1 0 1.3.2 2.5.6 3.6.1.3 0 .7-.2 1z"/></svg>08 9470 3318</li>
      <li><svg viewBox="0 0 24 24" aria-hidden="true"><path d="M7 1h10a2 2 0 0 1 2 2v18a2 2 0 0 1-2 2H7a2 2 0 0 1-2-2V3a2 2 0 0 1 2-2zm0 3v13h10V4zm5 15a1.3 1.3 0 1 0 0 2.6 1.3 1.3 0 0 0 0-2.6z"/></svg>123-456-7890</li>
      <li><svg viewBox="0 0 24 24" aria-hidden="true"><path d="M7 2h10v5H7zM4 8h16a2 2 0 0 1 2 2v7h-4v5H6v-5H2v-7a2 2 0 0 1 2-2zm4 8v4h8v-4z"/></svg>08 9470 3319</li>
      <li><svg viewBox="0 0 24 24" aria-hidden="true"><path d="M2 5h20v14H2zm2 2v.4l8 5.2 8-5.2V7zm0 2.8V17h16V9.8l-8 5.2z"/></svg>sales@tarvoplastics.com.au</li>
    </ul>
  </div>
  <div class="name-band"><span class="person-name">Your Name,</span><span class="person-title">Title</span></div>
</section>

<section class="card card-back" aria-label="Business card back">
  <div class="back-content">
    <p class="markets">The Products And Services That We Offer<br>Are Supplied From Diy To Trade &amp; Industrial Engineering Markets</p>
    <h2 class="section-title">We specialise in:</h2>
    <ul class="offer-list">
      <li><span>Cut to size panels (all shapes and sizes)</span></li>
      <li><span>Plastics fabrication &amp; Welding</span><span>Custom Designs</span></li>
      <li><span>Plastic Repairs</span><span>PVC Pipe Slotting &amp; PVC Pipe Threading</span></li>
      <li><span>Supplier of all types of engineering plastics and profiles</span></li>
    </ul>
    <h2 class="section-title">Including:</h2>
    <ul class="offer-list">
      <li><span>Acrylic / Clarvene</span><span>Polycarbonate / Dorvil</span></li>
      <li><span>Prismatic Light Diffuser</span><span>Vantrib</span><span>HDPE / UHMWPE</span></li>
      <li><span>PVC / PVC Foam</span><span>Nylon</span><span>HIPS</span></li>
    </ul>
  </div>
</section>

</body>
</html>
```